Marlow Estate Fixers (Handyman / Home Improvement Company)

Looking for a double sided professional looking business card with Logo attached to be highlighted on one side and throwing in an image of a handyman as an option would be nice to see as well. We are a company focused on providing quality Handyman and Home improvement services in a timely manner that is done right the first time with integrity

Industry/Entity Type

Handyman / Home Improvement

Contact Information for Business Card

(LOGO, Name, Mobile and office phone numbers, email) on front side of card, (the words "The SOLUTION to all of your Handyman and Home Improvement needs" followed by "Family Owned and Operated" at the very bottom) on the back.

Colors
EB3D1F
EC4F4E
F09395
F8D3D4
FCEDEE

Requirements
Must have
• Red, Gray, Black Color scheme
Should not have
• No Yellow or Blue colors

```html
<!DOCTYPE html>
<html lang="en">
<head>
<meta charset="utf-8">
<title>Marlow Estate Fixers – Business Card</title>
<link href="https://fonts.googleapis.com/css2?family=Poppins:wght@400;500;600;700&display=swap" rel="stylesheet">
<style>
  :root {
    --page-bg: #f0f0f0;
    --card-bg: #222226;
    --card-emboss: #2f2f34;
    --accent-red: #ec1c24;
    --text-white: #ffffff;
  }
  * { box-sizing: border-box; margin: 0; padding: 0; }
  html, body {
    width: 1200px; height: 990px; overflow: hidden;
    background: var(--page-bg);
    font-family: "Poppins", sans-serif;
    color: var(--text-white);
  }
  .card-slot { position: absolute; left: 244px; width: 712px; height: 405px; }
  .card-slot--back { top: 68px; }
  .card-slot--front { top: 516px; }
  .card-edge {
    position: absolute; left: -5px; top: 4px; width: 712px; height: 405px;
    background: var(--accent-red); border-radius: 30px;
  }
  .card {
    position: absolute; inset: 0; background: var(--card-bg);
    border-radius: 30px; overflow: hidden;
  }
  /* back side */
  .brand-emboss {
    position: absolute; left: 0; right: 0; top: 150px;
    display: flex; align-items: center; justify-content: center; gap: 14px;
    font-weight: 700; font-size: 34px; color: var(--card-emboss);
  }
  .brand-emboss .brand-mark { width: 22px; height: 22px; background: var(--card-emboss); }
  .tagline { position: absolute; left: 0; right: 0; text-align: center; font-size: 17px; letter-spacing: 0.3px; }
  .tagline--family { top: 333px; color: var(--accent-red); }
  .tagline--solution { top: 355px; }
  /* front side */
  .brand-name {
    position: absolute; right: 24px; top: 58px;
    display: flex; align-items: center; gap: 10px;
    font-weight: 700; font-size: 24px; color: var(--text-white);
  }
  .brand-name .brand-mark { width: 16px; height: 16px; background: var(--accent-red); }
  .name-bar { position: absolute; left: 0; top: 175px; width: 19px; height: 53px; background: var(--accent-red); }
  .person-name { position: absolute; left: 27px; top: 168px; font-size: 38px; font-weight: 400; line-height: 1.2; }
  .person-name .first { color: var(--accent-red); font-weight: 600; }
  .person-role { position: absolute; left: 27px; top: 212px; font-size: 18px; font-weight: 500; }
  .role-rule { position: absolute; left: 209px; right: 0; top: 222px; height: 2px; background: var(--text-white); }
  .contact-list { position: absolute; left: 27px; top: 262px; list-style: none; }
  .contact-list li { display: flex; align-items: center; gap: 10px; font-size: 18px; height: 24.5px; }
  .contact-list svg { width: 16px; height: 16px; fill: var(--accent-red); }
  .contact-list .hl { color: var(--accent-red); }
  .address { position: absolute; right: 26px; top: 309px; text-align: right; font-size: 18px; line-height: 26px; }
  .bottom-band { position: absolute; left: 0; bottom: 0; }
</style>
</head>
<body>

<section class="card-slot card-slot--back">
  <div class="card-edge"></div>
  <div class="card">
    <div class="brand-emboss"><span class="brand-mark"></span>Marlow Estate Fixers</div>
    <p class="tagline tagline--family">Family Owned and Operated</p>
    <p class="tagline tagline--solution">Your SOLUTION to all of your Handyman and Home Improvement needs</p>
  </div>
</section>

<section class="card-slot card-slot--front">
  <div class="card-edge"></div>
  <div class="card">
    <div class="brand-name"><span class="brand-mark"></span>Marlow Estate Fixers</div>

    <div class="name-bar"></div>
    <h1 class="person-name"><span class="first">Renata</span> Voss</h1>
    <p class="person-role">Founder &amp; CEO</p>
    <div class="role-rule"></div>

    <ul class="contact-list">
      <li><svg viewBox="0 0 16 16"><path d="M4 0h8a1 1 0 0 1 1 1v14a1 1 0 0 1-1 1H4a1 1 0 0 1-1-1V1a1 1 0 0 1 1-1zm1 2v11h6V2z"/></svg>(555) 214-3368</li>
      <li><svg viewBox="0 0 16 16"><path d="M3 1l3 3-2 2c1 2 3 4 6 6l2-2 3 3-2 3C7 15 1 9 0 3z"/></svg>(555) 480-1190</li>
      <li><svg viewBox="0 0 16 16"><path d="M8 0a8 8 0 1 0 0 16A8 8 0 0 0 8 0zm0 2a6 6 0 0 1 0 12A6 6 0 0 1 8 2z"/><path d="M4 5h4v3H5zM9 9h3l-1 3H9z"/></svg>www.<span class="hl">marlowfixers</span>.com</li>
      <li><svg viewBox="0 0 16 16"><path d="M0 3h16v11H0zm2 2v.5L8 9l6-3.5V5z"/></svg>info@<span class="hl">marlowfixers</span>.com</li>
    </ul>

    <p class="address">418 Alder Crest Rd. Suite<br>120 Brookfield, TX 75099</p>

    <svg class="bottom-band" width="712" height="405" viewBox="0 0 712 405" aria-hidden="true">
      <path d="M0 375 H410 L420 379 H0 Z" fill="var(--accent-red)"/>
      <path d="M0 383 H410 Q420 383 430 390 L452 405 H0 Z" fill="var(--text-white)"/>
      <path d="M425 375 H712 V405 H468 Z" fill="var(--accent-red)"/>
    </svg>
  </div>
</section>

</body>
</html>
```